business card

Business card for new business.
Red and black corporate colors.
Card can have an Indsutrial feel to it. Feel free to add Rust, Bolted steel, or graphics as you see fit. We provide highly specialized services to the below mentioned industries.
Keep information out of corners so that if I want I can choose rounded corners.
Information
- front. name - title - phone - email
- Rear
Refining - Rail - Infrastructure - Mining - Energy
Calgary - Edmonton - Fort McMurray - Revelstoke - Vancouver

```html
<!DOCTYPE html>
<html lang="en">
<head>
<meta charset="utf-8">
<title>Ironvale Business Card</title>
<link rel="stylesheet" href="https://fonts.googleapis.com/css2?family=Arimo:wght@400;700&display=swap">
<style>
  :root {
    --backdrop: #2b2b2b;
    --card: #050505;
    --brand-red: #e3202a;
    --steel-grey: #8c8c8c;
    --light-grey: #b3b3b3;
  }
  * { margin: 0; padding: 0; box-sizing: border-box; }
  html, body {
    width: 1200px;
    height: 880px;
    overflow: hidden;
    background: var(--backdrop);
    font-family: "Arimo", Arial, sans-serif;
  }
  .sheet {
    position: relative;
    width: 1200px;
    height: 880px;
  }
  .card {
    position: absolute;
    left: 270px;
    width: 660px;
    height: 377px;
    background: var(--card);
    border-radius: 22px;
    border-bottom: 6px solid var(--brand-red);
    box-shadow: 0 10px 30px rgba(0,0,0,0.55);
  }
  .card--back { top: 38px; }
  .card--front { top: 463px; }

  .brand-name {
    font-weight: 700;
    color: var(--steel-grey);
    letter-spacing: 2px;
    line-height: 1;
  }
  .card--back .brand-name {
    position: absolute;
    left: 0; right: 0;
    top: 150px;
    text-align: center;
    font-size: 68px;
  }
  .card--front .brand-name {
    position: absolute;
    left: 160px;
    top: 66px;
    font-size: 58px;
  }

  .identity {
    position: absolute;
    right: 370px;
    top: 178px;
    text-align: right;
  }
  .identity__name {
    font-weight: 700;
    font-size: 19px;
    color: var(--steel-grey);
    letter-spacing: 0.5px;
  }
  .identity__title {
    font-size: 16px;
    color: var(--brand-red);
    margin-top: 2px;
  }

  .divider {
    position: absolute;
    left: 308px;
    top: 160px;
    width: 2px;
    height: 74px;
    background: var(--brand-red);
  }

  .contact-list {
    position: absolute;
    left: 326px;
    top: 160px;
    list-style: none;
  }
  .contact-list li {
    display: flex;
    align-items: center;
    gap: 8px;
    font-size: 16px;
    color: var(--light-grey);
    height: 24px;
  }
  .contact-list svg { width: 14px; height: 14px; flex: none; }

  .coverage {
    position: absolute;
    left: 0; right: 0;
    top: 278px;
    text-align: center;
    font-size: 16px;
    color: var(--steel-grey);
    line-height: 25px;
  }
  .coverage .sep { color: var(--brand-red); padding: 0 4px; }
</style>
</head>
<body>
<main class="sheet">
  <section class="card card--back" aria-label="Card back">
    <div class="brand-name">IRONVALE</div>
  </section>

  <section class="card card--front" aria-label="Card front">
    <div class="brand-name">IRONVALE</div>

    <div class="identity">
      <div class="identity__name">JORDAN REEVE</div>
      <div class="identity__title">Managing Director</div>
    </div>

    <div class="divider"></div>

    <ul class="contact-list">
      <li>
        <svg viewBox="0 0 16 16" aria-hidden="true"><path fill="#e3202a" d="M3 1.5l2.5-.5 1.5 3.5-1.8 1.2a9 9 0 0 0 4.6 4.6L11 8.5l3.5 1.5-.5 2.5c-.3 1.2-1.5 2-2.8 1.8C6 13.5 2.5 10 1.7 4.3 1.5 3 2 1.8 3 1.5z"/></svg>
        (01) 5550 1234
      </li>
      <li>
        <svg viewBox="0 0 16 16" aria-hidden="true"><rect x="1" y="3" width="14" height="10" fill="#e3202a"/><path d="M1.5 3.5L8 9l6.5-5.5" fill="none" stroke="#050505" stroke-width="1.3"/></svg>
        info@ironvale.com
      </li>
      <li>
        <svg viewBox="0 0 16 16" aria-hidden="true"><g fill="none" stroke="#e3202a" stroke-width="1.4"><circle cx="8" cy="8" r="6.5"/><ellipse cx="8" cy="8" rx="2.8" ry="6.5"/><path d="M1.5 8h13M2.5 5h11M2.5 11h11"/></g></svg>
        www.ironvale.com
      </li>
    </ul>

    <p class="coverage">
      Refining<span class="sep">|</span>Rail<span class="sep">|</span>Infrastructure<span class="sep">|</span>Mining<span class="sep">|</span>Energy<br>
      Calgary<span class="sep">|</span>Edmonton<span class="sep">|</span>Fort McMurray<span class="sep">|</span>Revelstoke<span class="sep">|</span>Vancouver
    </p>
  </section>
</main>
</body>
</html>
```